Business Card Design

We need a business card designed for our new company. Prefer a black card with white logo & writing.

Contact Information for Business Card

Ted Galloway, address: 7-4812 Fernhollow Road, Abbotsford, BC, V3K 8R2, Office Phone: 604-712-3390, Cell: 604-947-2164, Email: ted@resinworkshub.ca

Colors

Designer to choose only greyscale colors for use in the design.

```html
<!DOCTYPE html>
<html lang="en">
<head>
<meta charset="utf-8">
<title>Resinworks Hub – Business Card</title>
<link href="https://fonts.googleapis.com/css2?family=Montserrat:wght@400;600;800&display=swap" rel="stylesheet">
<style>
  :root {
    --backdrop: #232323;
    --card: #000000;
    --ink-light: #ffffff;
    --ink-dark: #111111;
  }
  * { margin: 0; padding: 0; box-sizing: border-box; }
  html, body { width: 1200px; height: 900px; overflow: hidden; }
  body {
    background: var(--backdrop);
    font-family: "Montserrat", sans-serif;
    position: relative;
  }
  .card {
    position: absolute;
    left: 341px;
    width: 518px;
    height: 296px;
    background: var(--card);
    overflow: hidden;
  }
  .card--front { top: 141px; }
  .card--back { top: 463px; }

  .wordmark {
    position: absolute;
    left: 0; right: 0;
    display: flex;
    align-items: center;
    justify-content: center;
    gap: 10px;
    color: var(--ink-light);
    font-weight: 800;
    letter-spacing: 0.5px;
    white-space: nowrap;
  }
  .wordmark__dot {
    background: var(--ink-light);
    border-radius: 50%;
    flex: none;
  }
  .card--front .wordmark { top: 28px; font-size: 30px; }
  .card--front .wordmark__dot { width: 18px; height: 18px; }
  .card--back .wordmark { top: 126px; font-size: 36px; }
  .card--back .wordmark__dot { width: 22px; height: 22px; }

  .contact-panel { position: absolute; left: 0; top: 0; }

  .person-name {
    position: absolute;
    top: 174px;
    left: 0; right: 0;
    text-align: center;
    font-size: 18px;
    font-weight: 800;
    color: var(--ink-dark);
    letter-spacing: 0.3px;
  }
  .contact-list {
    position: absolute;
    top: 220px;
    font-size: 12.5px;
    line-height: 18px;
    color: var(--ink-dark);
    list-style: none;
  }
  .contact-list--reach { right: 276px; text-align: right; }
  .contact-list--place { left: 276px; }
  .contact-list li { display: flex; align-items: center; gap: 5px; }
  .contact-list--reach li { justify-content: flex-end; }
  .contact-list svg { width: 12px; height: 12px; flex: none; }
  .web-domain { font-weight: 800; }
  .divider {
    position: absolute;
    left: 260px;
    top: 222px;
    width: 1px;
    height: 47px;
    background: var(--ink-dark);
  }
</style>
</head>
<body>

<section class="card card--front">
  <div class="wordmark">Resinworks Hub<span class="wordmark__dot"></span></div>

  <svg class="contact-panel" width="518" height="296" viewBox="0 0 518 296">
    <polygon points="256,109 465,230 465,296 48,296 48,230" fill="var(--ink-light)"/>
  </svg>

  <p class="person-name">TED GALLOWAY</p>

  <ul class="contact-list contact-list--reach">
    <li>604-712-3390
      <svg viewBox="0 0 24 24"><path d="M6.6 10.8a15 15 0 0 0 6.6 6.6l2.2-2.2c.3-.3.7-.4 1-.2 1.1.4 2.3.6 3.6.6.6 0 1 .4 1 1V20c0 .6-.4 1-1 1A17 17 0 0 1 3 4c0-.6.4-1 1-1h3.5c.6 0 1 .4 1 1 0 1.3.2 2.5.6 3.6.1.3 0 .7-.2 1z" fill="var(--ink-dark)"/></svg>
    </li>
    <li>604-947-2164
      <svg viewBox="0 0 24 24"><rect x="6" y="2" width="12" height="20" rx="2" fill="none" stroke="var(--ink-dark)" stroke-width="2"/><circle cx="12" cy="18" r="1.2" fill="var(--ink-dark)"/></svg>
    </li>
    <li>ted@resinworkshub.ca
      <svg viewBox="0 0 24 24"><path d="M2 6h20v13H2z" fill="var(--ink-dark)"/><path d="M2 6l10 7 10-7" fill="none" stroke="var(--ink-light)" stroke-width="1.6"/></svg>
    </li>
  </ul>

  <span class="divider"></span>

  <ul class="contact-list contact-list--place">
    <li>7-4812 Fernhollow Road</li>
    <li>Abbotsford, BC, V3K 8R2</li>
    <li>
      <svg viewBox="0 0 24 24" fill="none" stroke="var(--ink-dark)" stroke-width="1.6"><circle cx="12" cy="12" r="10"/><ellipse cx="12" cy="12" rx="4.5" ry="10"/><path d="M2 12h20M4 7h16M4 17h16"/></svg>
      <span><span class="web-domain">resinworkshub</span>.ca</span>
    </li>
  </ul>
</section>

<section class="card card--back">
  <div class="wordmark">Resinworks Hub<span class="wordmark__dot"></span></div>
</section>

</body>
</html>
```